Varnex Consulting Business card design.

See our website www.varnexconsulting.example which will give you a good idea of what we are about. The font is called 'Play'.

I'd like a standout business card in keeping with the themes and branding on the website

Target Market(s)

professionals. HR directors

Industry/Entity Type

Business

Contact Information for Business Card

Varnex Consulting PO Box 3172 Merrowdale NSW 2291 1300 485 193 Gavin Threlkeld Principal email: career@varnexconsulting.example ABN: 71203948865

Font styles to use
Other font styles liked:
• Play

Requirements
Must have
• Must have same design colours and branding as website.
• On back I'd prefer a list of the things we do which appears below the name at the header on the website

```html
<!DOCTYPE html>
<html lang="en">
<head>
<meta charset="utf-8">
<title>Varnex Consulting – Business Card</title>
<link rel="stylesheet" href="https://fonts.googleapis.com/css2?family=Play:wght@400;700&family=Arimo:wght@400;700&display=swap">
<style>
  :root {
    --bg: #e4e2de;
    --card-light: #ffffff;
    --card-shade: #d8d8d8;
    --navy: #1b2a3a;
    --navy-deep: #14202d;
    --blue: #1f8fdc;
    --text: #222a33;
    --muted: #5c5f63;
    --rule: #9a9a9a;
  }
  * { box-sizing: border-box; margin: 0; padding: 0; }
  html, body { width: 1200px; height: 950px; overflow: hidden; }
  body {
    background: var(--bg);
    font-family: "Arimo", Arial, sans-serif;
    color: var(--text);
    position: relative;
  }
  .card {
    position: absolute;
    left: 240px;
    width: 720px;
    height: 411px;
    overflow: hidden;
    box-shadow: 0 6px 18px rgba(0,0,0,0.18);
  }
  .card--back {
    top: 40px;
    background: linear-gradient(100deg, var(--card-light) 0%, #f1f1f1 45%, var(--card-shade) 100%);
  }
  .card--front {
    top: 499px;
    background: linear-gradient(110deg, var(--card-light) 0%, #f6f6f6 55%, #e6e6e6 100%);
  }
  .wordmark {
    position: absolute;
    font-family: "Play", sans-serif;
    font-weight: 400;
    font-size: 31px;
    letter-spacing: 3px;
    color: var(--navy);
    white-space: nowrap;
  }
  .card--back .wordmark { left: 190px; top: 150px; }
  .services {
    position: absolute;
    right: 60px;
    top: 215px;
    font-size: 15px;
    color: var(--muted);
    letter-spacing: 0.5px;
  }
  .card--front .wordmark { right: 44px; top: 72px; }
  .person { position: absolute; left: 42px; top: 148px; }
  .person__name { font-size: 22px; font-weight: 700; color: var(--text); }
  .person__role { font-size: 15px; color: var(--blue); margin-top: 3px; }
  .divider {
    position: absolute;
    left: 128px; right: 40px; top: 197px;
    height: 1px;
    background: var(--rule);
  }
  .contact { position: absolute; left: 42px; top: 214px; list-style: none; }
  .contact li {
    display: flex; align-items: center; gap: 8px;
    font-size: 15px; color: var(--text);
    margin-bottom: 8px;
  }
  .contact svg { width: 15px; height: 15px; fill: var(--text); }
  .address {
    position: absolute;
    right: 64px; top: 262px;
    text-align: right;
    font-size: 17px;
    line-height: 1.4;
    color: var(--muted);
    font-style: normal;
  }
  .footer-band { position: absolute; left: 0; bottom: 0; width: 720px; height: 75px; }
  .website {
    position: absolute;
    right: 44px; bottom: 18px;
    font-size: 17px;
    color: #ffffff;
    letter-spacing: 0.3px;
  }
</style>
</head>
<body>

  <section class="card card--back" aria-label="Card back">
    <div class="wordmark">VARNEX CONSULTING</div>
    <p class="services">Coaching | Leadership | Outplacement</p>
  </section>

  <section class="card card--front" aria-label="Card front">
    <div class="wordmark">VARNEX CONSULTING</div>

    <div class="person">
      <h1 class="person__name">Gavin Threlkeld</h1>
      <p class="person__role">Principal</p>
    </div>
    <div class="divider"></div>

    <ul class="contact">
      <li>
        <svg viewBox="0 0 16 16" aria-hidden="true"><path d="M2 5c0-2 2-3 6-3s6 1 6 3v1h-3V5H5v1H2z M4 7h8l2 6H2z M8 8.5a2 2 0 1 0 0.01 0z"/></svg>
        1300 485 193
      </li>
      <li>
        <svg viewBox="0 0 16 16" aria-hidden="true"><path d="M1 3h14v10H1z M2 4.2v0.6l6 4 6-4v-0.6z" fill-rule="evenodd"/></svg>
        career@varnexconsulting.example
      </li>
    </ul>

    <address class="address">PO Box 3172 Merrowdale<br>NSW 2291</address>

    <svg class="footer-band" viewBox="0 0 720 75" aria-hidden="true">
      <rect x="0" y="0" width="450" height="16" fill="var(--blue)"/>
      <polygon points="430,0 720,0 720,75 382,75" fill="var(--navy)"/>
      <polygon points="430,0 720,0 720,6 426,6" fill="var(--navy-deep)"/>
    </svg>
    <div class="website">www.varnexconsulting.example</div>
  </section>

</body>
</html>
```